2-Page Flyer for the Information Session about the Quiet Pathfinder Course

This is a flyer to announce/advertise an evening Information Session about the Quiet Pathfinder Course. This Program aims at mindfully rethinking and redesigning work (and life) for people who feel stuck or not entirely satisfied with their work and/or life (please see draft flyer attached for more details). This Program is property of Bright Meadow, a company that uses a combination of Mindfulness, Design, and Entrepreneurship to help people achieve greater happiness (in their work and lives).

Target Market(s)

People who feel stuck or not entirely satisfied with their work and/or life (please see draft flyer attached for more details)

Font styles to use
Serif
Sans Serif

Colors
ffffff
f37122
33a6d7
acd037

Requirements
Must have
• All of what I will say below is suggestive (I’m not a design expert), and I’m open to divert from it, if it makes sense and feels more interesting.
• I thought initially of a 2-page flyer (please see draft flyer attached). The first page could help people grasp the essence of the event quickly (in 1 or 2 minutes), and then, if they are interested/motivated, they would continue reading through page 2, which has more info about the Program in itself.
• Potential Structure
• Page 1
• . About the Information Session on the Quiet Pathfinder Course
• . Visible Date & Time, Contacts, Venue (and other relevant info)
• . About me (the facilitator)
• Page 2
• . About the Quiet Pathfinder Course
• I include a Powerpoint draft of the flyer with the content. The design is rudimentary and precarious from an aesthetics/organization point of view, and this is mainly where I need help (and maybe in other aspects too!).
• On the flyer, I would like to include:
• . A photo of myself (I attach 1 picture).
• . 1 or 2 beautiful-nature photos (cropped or full). One may have to do with looking at the sky, dreaming, and imagining a new work and life (2 photos with sky and clouds attached). The other has to do with walking the transformation journey (the photo with the person walking through the forest path).
• . bright meadow logo or logos (there are two slightly different ones, that can be used for different purposes). For the first page, I would like the bright meadow logo that has "bright meadow" written on the bottom, with the saying "Stillness, Craft and Venture for Bright Meadow" beneath. This is the main logo. For the 2nd page, you can choose the logo that adapts better.
• - Where it says the "the way out is in" it would be great to have a similar font to the one I attach (see file "Font_the_way_out_is_in.png" and Ankecallig-fg.ttf
Nice to have
• In terms of colours, I would not divert much from the logo colours (and of course white and black). I would like the flyer to be quite white. Almost like fairy-tale white: the white horse, the white snow, the white of the stars, the white heaven. White could be the base colour. White means peace, tranquillity, calm contentment, a smile.
• And then use the other colours. The green of the mindfulness. The blue of the sky, the dreams. And the orange of the sun, the energy, the fire, the action. And maybe the black for text.
• Where it says the "the way out is in" it would be great to have a similar font to the one I attach (see file "Font_the_way_out_is_in".
• I would like this flyer to be a piece of art, in every possible way. Simple, beautiful, ease, light, peaceful, calm happy. Just like the Quiet Pathfinder Course and bright meadow Company that I am creating intends to be. The mission of this Program and Company is to be a designer, a painter (a Picasso) of happier and more fulfilling human lives.
• I am very much looking forward to seeing your proposal(s).

```html
<!DOCTYPE html>
<html lang="en">
<head>
<meta charset="utf-8">
<title>Bright Meadow – Quiet Pathfinder Course Flyer</title>
<link href="https://fonts.googleapis.com/css2?family=Oswald:wght@500;600&family=Montserrat:wght@500;700;800&family=Source+Sans+3:ital,wght@0,400;0,600;0,700;1,400;1,600&family=Caveat:wght@600&display=swap" rel="stylesheet">
<style>
  :root{
    --orange:#f37122;
    --blue:#33a6d7;
    --green:#acd037;
    --white:#ffffff;
    --ink:#222425;
    --mist:#e8eff3;
    --paper:#f1f2f2;
    --stage:#dcdfe0;
    --night:#111213;
  }
  *{box-sizing:border-box;margin:0;padding:0}
  html,body{width:1200px;height:878px;overflow:hidden;background:var(--stage)}
  body{position:relative;font-family:"Source Sans 3",Arial,sans-serif;color:var(--ink)}
  .page{position:absolute;top:77px;width:512px;height:724px;background:var(--white);overflow:hidden}
  .page--front{left:82px}
  .page--back{left:614px}
  .abs{position:absolute}

  /* brand wordmark */
  .wordmark{font-family:"Source Sans 3",sans-serif;font-weight:400;color:var(--blue);white-space:nowrap;line-height:1}
  .brand-dot{position:absolute;border-radius:50%;background:var(--green)}

  /* front */
  .hero-visual{left:222px;top:0;width:300px;height:330px;border-radius:48% 40% 46% 52%;
    background:linear-gradient(135deg,#8cc4e6 0%,#cfe6f2 30%,#6f9a3a 58%,#4d7a24 75%,#e37a33 100%)}
  .title-band{left:0;top:106px;width:256px;height:156px;background:var(--blue)}
  .title{left:20px;color:var(--white);font-family:"Oswald",sans-serif;font-weight:600;line-height:1;letter-spacing:.5px}
  .tagline-band{left:0;top:262px;width:272px;height:62px;background:var(--green)}
  .tagline{left:20px;top:274px;font-style:italic;font-size:15px;line-height:19px;color:var(--ink)}
  .section-head{font-family:"Source Sans 3",sans-serif;font-weight:700;color:var(--orange);font-size:17px}
  .body-copy{font-size:9.2px;line-height:11.6px;color:#333}
  .facilitator-zone{left:0;top:458px;width:512px;height:176px;background:linear-gradient(180deg,#f7f7f7,#e9eaea)}
  .portrait{left:24px;top:482px;width:136px;height:136px;border-radius:50%;border:3px solid var(--white);
    background:radial-gradient(circle at 50% 40%,#d9c9c4,#8a8f96 70%,#5d6470)}
  .fac-name{font-family:"Source Sans 3",sans-serif;font-weight:700;color:var(--orange);font-size:22px;letter-spacing:-.3px}
  .bio{font-size:6.4px;line-height:8.7px;color:#333;text-align:justify}
  .link{color:var(--blue);font-weight:700}
  .strip-note{font-family:"Montserrat",sans-serif;font-size:5.6px;letter-spacing:4px;color:#cfcfcf}

  /* back */
  .back-header{left:0;top:0;width:512px;height:70px;background:linear-gradient(180deg,#f4f4f4,#e9e9e9)}
  .intro-band{left:0;top:80px;width:512px;height:100px;background:var(--blue)}
  .intro-title{left:0;top:94px;width:512px;text-align:center;font-family:"Montserrat",sans-serif;font-weight:800;font-size:23.5px;color:var(--white)}
  .intro-copy{left:24px;top:136px;width:468px;font-style:italic;font-size:8.7px;line-height:11.3px;color:var(--white)}
  .program-zone{left:0;top:180px;width:512px;height:222px;background:var(--mist)}
  .blue-head{color:var(--blue)}
  .green-head{color:#8dba20}
  .text-layer{z-index:2}
  .steps{list-style:none}
  .steps li{position:relative;padding-left:12px;font-size:8.4px;line-height:10px;margin-bottom:1.5px}
  .steps .num{position:absolute;left:0;top:.5px;width:9px;height:9px;border-radius:50%;color:var(--white);font-size:6.5px;font-weight:700;text-align:center;line-height:9px}
  .num--orange{background:var(--orange)}
  .num--green{background:var(--green)}
  .landscape{left:0;top:556px;width:512px;height:74px;z-index:1;
    background:linear-gradient(180deg,rgba(255,255,255,0) 0%,#b9c8d2 30%,#7d8f98 60%,#566a55 100%)}
  .motto-band{left:0;top:630px;width:512px;height:48px;background:var(--orange)}
  .motto{left:0;top:632px;width:512px;text-align:center;font-family:"Caveat",cursive;font-weight:600;font-size:34px;color:var(--white)}
  .contact-band{left:0;top:678px;width:512px;height:34px;background:var(--blue)}
  .night-strip{left:0;top:712px;width:512px;height:12px;background:var(--night)}
  .contact-text{font-family:"Montserrat",sans-serif;font-weight:700;font-size:10px;color:var(--ink);white-space:nowrap}
</style>
</head>
<body>

<!-- FRONT PAGE -->
<section class="page page--front">
  <span class="brand-dot" style="left:88px;top:26px;width:40px;height:40px"></span>
  <div class="abs wordmark" style="left:34px;top:76px;font-size:24px">bright meadow</div>

  <div class="abs hero-visual" role="img" aria-label="Nature photo collage: blue sky with clouds, green hills and an orange sunset sky"></div>

  <div class="abs title-band"></div>
  <div class="abs title" style="top:114px;font-size:56px">QUIET</div>
  <div class="abs title" style="top:174px;font-size:29px;font-weight:500">PATHFINDER</div>
  <div class="abs title" style="top:204px;font-size:56px">COURSE</div>

  <div class="abs tagline-band"></div>
  <div class="abs tagline">Stillness, Craft and Venture<br>for Bright Meadow</div>

  <h2 class="abs section-head" style="left:18px;top:330px">Information Session</h2>
  <p class="abs body-copy" style="left:18px;top:356px;width:478px">The purpose of this Information Session is to give you a real insight into the Quiet Pathfinder Course and how it can help you get the most out of your work and life.</p>

  <h2 class="abs section-head" style="left:20px;top:387px">Who can come</h2>
  <p class="abs body-copy" style="left:20px;top:412px;width:476px;text-align:justify">The Information Session is free and whether you come on your own, or with friends or family, you'll be warmly welcome. It will take place on Thursday the 23rd July 2019, from 19:30 to 21:00, at Tidewell Coworking. Please get in touch for more info or to book a place.</p>

  <div class="abs facilitator-zone"></div>
  <div class="abs portrait" role="img" aria-label="Portrait photo of the facilitator"></div>

  <div class="abs" style="left:182px;top:478px;font-size:9px;font-weight:600">Facilitator</div>
  <div class="abs fac-name" style="left:181px;top:490px">DR MARCO ELLISON</div>
  <div class="abs" style="left:182px;top:516px;font-size:9.5px;font-style:italic;font-weight:600">Visiting Research Fellow, Northvale University</div>
  <p class="abs bio" style="left:182px;top:530px;width:313px">Marco joined Northvale University (School of Management) as a Lecturer in Entrepreneurship in 2015. He completed his PhD in Entrepreneurship at Kelmore Business School in 2014. His work received the Ashby Doctoral Award from the Academy of Enterprise Studies. He began his business career as a production engineer (Corvan), and continued in sales (Altrix). After his MBA, he worked as a strategy consultant at Harbour Business School. Originally from Portugal, Marco enjoys designing and launching new ideas, international communities, mindfulness retreats, and musical improvisation. He nurtures a close connection to Linden Grove Retreat Centre, where he has practiced and volunteered over 9 months. He has a broad experience of sharing the benefits of mindfulness with others.</p>
  <div class="abs" style="left:182px;top:608px;font-size:11.5px">More about the facilitator: <span class="link">www.brightmeadow.io/marco</span></div>

  <svg class="abs" style="left:0;top:630px" width="512" height="94" viewBox="0 0 512 94" aria-hidden="true">
    <polygon points="0,0 300,0 262,46 0,46" fill="#f37122"/>
    <polygon points="300,0 322,0 264,82 0,82 0,46 262,46" fill="#33a6d7"/>
    <polygon points="322,0 512,0 512,82 264,82" fill="#acd037"/>
    <rect x="0" y="82" width="512" height="12" fill="#111213"/>
    <circle cx="30" cy="64" r="12" fill="#111213"/>
    <path d="M24 60c0-2 2-3 6-3s6 1 6 3l-2 1-1-1h-6l-1 1zM25 62h10l1 7H24z" fill="#fff"/>
    <path d="M329 35c-3 0-5 2-5 5 0 3 5 8 5 8s5-5 5-8c0-3-2-5-5-5zm0 7a2 2 0 1 1 0-4 2 2 0 0 1 0 4z" fill="#222425"/>
    <circle cx="329" cy="54" r="4.5" fill="#222425"/>
    <path d="M326.5 52.5h5v3h-5zM326.5 52.5l2.5 2 2.5-2" fill="none" stroke="#fff" stroke-width=".8"/>
  </svg>
  <div class="abs" style="left:19px;top:634px;font-size:16px;font-weight:600;color:#fff">Information Session</div>
  <div class="abs" style="left:19px;top:655px;font-size:11.5px;color:#fff">Thursday 18th July 2019, from 19:30 to 21:00</div>
  <div class="abs" style="left:50px;top:683px;font-size:6px;color:#fff">For More Information</div>
  <div class="abs" style="left:50px;top:690px;font-family:Montserrat,sans-serif;font-weight:700;font-size:16px;color:#fff">+34 600 555 210</div>
  <div class="abs" style="left:325px;top:637px;font-family:Montserrat,sans-serif;font-weight:700;font-size:11px;color:var(--ink)">INFORMATION &amp; BOOKING:</div>
  <div class="abs" style="left:325px;top:652px;font-size:6px;color:#2a4a10">Please contact for more information or to book a place</div>
  <div class="abs" style="left:338px;top:663px;font-family:Montserrat,sans-serif;font-weight:500;font-size:7px">Tidewell Coworking, C/ Olmeda 14, Valencia</div>
  <div class="abs" style="left:338px;top:680px;font-family:Montserrat,sans-serif;font-weight:500;font-size:7px">hello@brightmeadow.io</div>
  <div class="abs strip-note" style="left:20px;top:714px">VIDEO CALL AND MESSAGING</div>
</section>

<!-- BACK PAGE -->
<section class="page page--back">
  <div class="abs back-header"></div>
  <span class="brand-dot" style="left:190px;top:17px;width:34px;height:34px"></span>
  <div class="abs wordmark" style="left:234px;top:16px;font-size:21px;line-height:19px">bright<br>meadow</div>
  <div class="abs" style="left:0;top:70px;width:512px;height:2px;background:var(--orange)"></div>
  <div class="abs" style="left:0;top:72px;width:512px;height:8px;background:var(--green)"></div>

  <div class="abs intro-band"></div>
  <svg class="abs" style="left:240px;top:179px" width="32" height="12" viewBox="0 0 32 12" aria-hidden="true"><polygon points="0,0 32,0 16,12" fill="#33a6d7"/></svg>
  <h1 class="abs intro-title">What is the Quiet Pathfinder Course</h1>
  <p class="abs intro-copy">Being mindful means being aware and awake. Entrepreneurship is the creation of a new form of organising. The Quiet Pathfinder Course is then the process of creating or redesigning your work and life with awareness, in a way that is reflective of you, of your passions and values, thus conducting to a greater sense of fulfilment and happiness.</p>

  <div class="abs program-zone"></div>
  <h2 class="abs section-head blue-head" style="left:21px;top:192px">The Program</h2>
  <p class="abs body-copy" style="left:21px;top:230px;width:222px;font-size:9.4px"><b>The Quiet Pathfinder Course</b> is a <b>4-month long transformative journey</b> designed for people who feel stuck or not entirely satisfied with their work and/or life. It is of benefit for everyone, at any stage.</p>
  <p class="abs body-copy" style="left:21px;top:298px;width:222px;font-size:9.4px">The Program consists of a 5-hour workshop each month, with 2-hour weekly peer support meetings. It combines mindfulness techniques, design thinking methodology, and entrepreneurship frameworks.</p>

  <svg class="abs" style="left:262px;top:184px" width="250" height="210" viewBox="0 0 250 210" role="img" aria-label="Cycle of four workshops joined by weekly peer support meetings">
    <circle cx="108" cy="98" r="80" fill="#ffffff" opacity=".6"/>
    <g font-family="Source Sans 3, sans-serif" font-weight="700" text-anchor="middle" fill="#fff">
      <circle cx="108" cy="36" r="30" fill="#fff"/><circle cx="108" cy="36" r="25" fill="#acd037"/>
      <text x="108" y="30" font-size="6.5">Workshop 1</text><text x="108" y="39" font-size="6.5">INSIGHT</text><text x="108" y="48" font-size="6">(5 hours)</text>
      <circle cx="170" cy="98" r="30" fill="#fff"/><circle cx="170" cy="98" r="25" fill="#33a6d7"/>
      <text x="170" y="92" font-size="6.5">Workshop 2</text><text x="170" y="101" font-size="6.5">DESIGN</text><text x="170" y="110" font-size="6">(5 hours)</text>
      <circle cx="108" cy="160" r="30" fill="#fff"/><circle cx="108" cy="160" r="25" fill="#f37122"/>
      <text x="108" y="154" font-size="6.5">Workshop 3</text><text x="108" y="163" font-size="6.5">EXECUTE</text><text x="108" y="172" font-size="6">(5 hours)</text>
      <circle cx="46" cy="98" r="30" fill="#fff"/><circle cx="46" cy="98" r="25" fill="#c5c7c8"/>
      <text x="46" y="92" font-size="6.5">Workshop 4</text><text x="46" y="101" font-size="6.5">PRESENT</text><text x="46" y="110" font-size="6">(5 hours)</text>
    </g>
    <path d="M142 44l12 12" stroke="#acd037" stroke-width="4"/><path d="M148 60l10 0 0-10z" fill="#acd037"/>
    <path d="M160 134l-12 12" stroke="#33a6d7" stroke-width="4"/><path d="M142 142l0 10 10 0z" fill="#33a6d7"/>
    <path d="M74 146l-12-12" stroke="#f37122" stroke-width="4"/><path d="M68 128l-10 0 0 10z" fill="#f37122"/>
    <path d="M58 58l12-12" stroke="#9a9c9d" stroke-width="4"/><path d="M74 52l0-10-10 0z" fill="#9a9c9d"/>
    <g font-family="Source Sans 3, sans-serif" font-weight="700" font-size="6.5" fill="#222425">
      <text x="2" y="34">WPS meetings</text>
      <text x="246" y="34" text-anchor="end">Weekly Peer Support</text>
      <text x="246" y="42" text-anchor="end">(WPS) meetings</text>
      <text x="236" y="50" text-anchor="end">(2 hours)</text>
      <text x="2" y="160">WPS meetings</text>
      <text x="246" y="159" text-anchor="end">WPS meetings</text>
    </g>
  </svg>

  <h2 class="abs section-head" style="left:22px;top:406px">Why</h2>
  <p class="abs body-copy" style="left:22px;top:429px;width:220px;font-size:8.4px;line-height:10px;text-align:justify">Many people are not satisfied with their work, but they don't know what to do about it. This Program offers you a safe place to conduct your inner journey with collective support, helping you reflect, design, and (very likely) do something about it. It aims at:</p>
  <ul class="abs steps text-layer" style="left:20px;top:484px;width:226px">
    <li><span class="num num--orange">1</span>Increasing awareness, clarity and confidence</li>
    <li><span class="num num--orange">2</span>Having a deeper <b><i>insight</i></b> on what makes you happier and what you want</li>
    <li><span class="num num--orange">3</span>Developing a clear <b><i>design</i></b> integrating your intended work and life</li>
    <li><span class="num num--orange">4</span>Start <b><i>executing</i></b> this design</li>
  </ul>

  <h2 class="abs section-head green-head" style="left:262px;top:406px">How</h2>
  <p class="abs body-copy" style="left:262px;top:429px;width:230px;font-size:8.4px;line-height:10px">This Program differs from existing entrepreneurial programs in many ways:</p>
  <ul class="abs steps text-layer" style="left:260px;top:458px;width:234px">
    <li><span class="num num--green">1</span>Uses mindfulness and self analysis to look deeply into your self</li>
    <li><span class="num num--green">2</span>Design and execution decisions are based on happiness rather than (only) financials</li>
    <li><span class="num num--green">3</span>Holistic and inclusive design process, integrating work and life, and building synergies between your different parts</li>
  </ul>
  <p class="abs body-copy text-layer" style="left:262px;top:530px;width:230px;font-size:8.4px;line-height:10px;text-align:justify">Format includes: lectures, individual work, group sharing, guided activities, experiential exercises, video, audio, handouts and other resources.</p>

  <div class="abs landscape" role="img" aria-label="Photo of a misty mountain landscape"></div>

  <div class="abs motto-band"></div>
  <div class="abs motto">“The Way Out is In”</div>

  <div class="abs contact-band"></div>
  <svg class="abs" style="left:20px;top:683px" width="24" height="24" viewBox="0 0 24 24" aria-hidden="true">
    <circle cx="12" cy="12" r="12" fill="#111213"/>
    <path d="M6 9c0-2 2-3 6-3s6 1 6 3l-2 1-1-1H9l-1 1zM7 11h10l1 7H6z" fill="#fff"/>
  </svg>
  <div class="abs contact-text" style="left:48px;top:689px">+34 600 555 210 (Video Call and Messaging)</div>
  <div class="abs" style="left:326px;top:684px;width:1.5px;height:22px;background:var(--ink)"></div>
  <svg class="abs" style="left:338px;top:683px" width="24" height="24" viewBox="0 0 24 24" aria-hidden="true">
    <circle cx="12" cy="12" r="12" fill="#111213"/>
    <rect x="6" y="8" width="12" height="8" fill="#fff"/>
    <path d="M6 8l6 5 6-5" fill="none" stroke="#111213" stroke-width="1.2"/>
  </svg>
  <div class="abs contact-text" style="left:367px;top:689px">hello@brightmeadow.io</div>
  <div class="abs night-strip"></div>
</section>

</body>
</html>
```